QVR business card

Need a business card for a company that provides instructional design and elearning development services. The website is here: http://quorvane.studio/

I'm attaching a current logo, as well as the old business card design. While I like to keep it clean, the old design is too simplistic for my liking. The only idea I want to reuse from the old design is placing industry jargon on the back of the card, just need a better way to present it. But if you have other ideas for the back--feel free to experiment.

Please use the colors complementary to the color we have on the website. Thank you!

```html
<!DOCTYPE html>
<html lang="en">
<head>
<meta charset="utf-8">
<title>QVR business card</title>
<link rel="stylesheet" href="https://fonts.googleapis.com/css2?family=Jost:wght@700&family=Roboto+Condensed:wght@700&family=Roboto:wght@400;500&display=swap">
<style>
  :root {
    --backdrop: #a9a7a7;
    --card-dark: #2c2c2e;
    --card-light: #f7f7f5;
    --teal: #1eb39f;
    --olive: #d9d186;
    --ink: #2f2f33;
    --ink-soft: #4a4a4f;
    --rule: #e2e2df;
    --white: #ffffff;
  }
  * { margin: 0; padding: 0; box-sizing: border-box; }
  html, body {
    width: 1200px; height: 1200px; overflow: hidden;
    background: var(--backdrop);
  }
  .canvas { position: relative; width: 1200px; height: 1200px; }

  .card {
    position: absolute;
    border-radius: 22px;
    overflow: hidden;
  }

  /* Reverse side: service terms */
  .card-reverse {
    left: 238px; top: 117px; width: 714px; height: 420px;
    background: var(--card-dark);
  }
  .card-reverse svg { display: block; }
  .term-line {
    font-family: "Jost", "Futura", sans-serif;
    font-weight: 700;
    font-size: 44px;
    fill: var(--teal);
  }
  .headline {
    font-family: "Roboto Condensed", "Arial Narrow", sans-serif;
    font-weight: 700;
    font-size: 82px;
    fill: var(--white);
  }
  .band-bar { fill: var(--white); }

  /* Front side: contact */
  .card-front {
    left: 231px; top: 645px; width: 712px; height: 416px;
    background: var(--card-light);
  }
  .brand {
    position: absolute;
    left: 0; top: 0; width: 363px; height: 416px;
    display: flex; align-items: center; justify-content: center; gap: 14px;
  }
  .brand-dot {
    width: 26px; height: 26px; border-radius: 50%;
    background: var(--teal);
  }
  .brand-name {
    font-family: "Roboto", sans-serif;
    font-weight: 500;
    font-size: 64px;
    letter-spacing: 4px;
    color: var(--teal);
  }
  .divider {
    position: absolute;
    left: 363px; top: 55px; width: 1px; height: 270px;
    background: var(--rule);
  }
  .person {
    position: absolute; left: 397px; top: 114px;
    font-family: "Roboto", sans-serif;
  }
  .person-name { font-weight: 500; font-size: 21px; color: var(--ink); letter-spacing: 0.4px; }
  .person-role { font-weight: 400; font-size: 16px; color: var(--ink-soft); margin-top: 6px; }
  .contacts {
    position: absolute; left: 397px; top: 205px;
    list-style: none;
    font-family: "Roboto", sans-serif; font-size: 17px; color: var(--ink);
  }
  .contacts li { display: flex; align-items: center; height: 27px; }
  .contacts svg { width: 16px; height: 16px; margin-right: 19px; fill: var(--teal); }

  .stripe-olive {
    position: absolute; left: 0; bottom: 0; width: 340px; height: 27px;
    background: var(--olive);
  }
  .stripe-teal {
    position: absolute; right: 0; bottom: 0; width: 400px; height: 53px;
    background: var(--teal);
    clip-path: polygon(31px 0, 100% 0, 100% 100%, 0 100%);
  }
  .email {
    position: absolute; left: 379px; bottom: 15px;
    font-family: "Roboto", sans-serif; font-size: 18px; color: var(--white);
    letter-spacing: 0.2px;
  }
</style>
</head>
<body>
<main class="canvas">

  <section class="card card-reverse" aria-label="Card reverse">
    <svg width="714" height="420" viewBox="0 0 714 420">
      <text class="term-line" x="42" y="60" textLength="630" lengthAdjust="spacingAndGlyphs">MICROLEARNING VIDEO UX</text>
      <text class="term-line" x="42" y="114" textLength="630" lengthAdjust="spacingAndGlyphs">STORYBOARDS ASSESSMENT</text>
      <text class="term-line" x="42" y="167" textLength="630" lengthAdjust="spacingAndGlyphs">AUTHORING TOOLS WCAG</text>
      <rect class="band-bar" x="0" y="180" width="30" height="60"/>
      <rect class="band-bar" x="688" y="180" width="26" height="60"/>
      <text class="headline" x="42" y="240" textLength="630" lengthAdjust="spacingAndGlyphs">WHAT SHALL WE BUILD?</text>
      <text class="term-line" x="42" y="286" textLength="630" lengthAdjust="spacingAndGlyphs">ONBOARDING SIMULATIONS</text>
      <text class="term-line" x="42" y="340" textLength="630" lengthAdjust="spacingAndGlyphs">KNOWLEDGE CHECKS COHORTS</text>
      <text class="term-line" x="42" y="393" textLength="630" lengthAdjust="spacingAndGlyphs">SCENARIO BASED TRAINING</text>
    </svg>
  </section>

  <section class="card card-front" aria-label="Card front">
    <div class="brand">
      <span class="brand-dot"></span>
      <span class="brand-name">QVR</span>
    </div>
    <div class="divider"></div>

    <div class="person">
      <p class="person-name">Maren Holloway</p>
      <p class="person-role">Managing Director</p>
    </div>

    <ul class="contacts">
      <li>
        <svg viewBox="0 0 16 16" aria-hidden="true"><path d="M1 6c0-2 3-4 7-4s7 2 7 4v1h-4V5.5c-1-.5-5-.5-6 0V7H1z"/><path d="M4 8h8l2 6H2z"/><circle cx="8" cy="11" r="1.6" fill="#f7f7f5"/></svg>
        <span>555-014-2087</span>
      </li>
      <li>
        <svg viewBox="0 0 16 16" aria-hidden="true"><circle cx="8" cy="8" r="7"/><path d="M1 8h14M8 1c-3 3-3 11 0 14M8 1c3 3 3 11 0 14" stroke="#f7f7f5" stroke-width="1.1" fill="none"/></svg>
        <span>www.quorvane.studio</span>
      </li>
    </ul>

    <div class="stripe-olive"></div>
    <div class="stripe-teal"></div>
    <p class="email">mholloway@quorvane.studio</p>
  </section>

</main>
</body>
</html>
```